Small Business Broker Business Card Design

A business card design for a small business brokerage, which is a financial service, not unlike real estate brokerage, but for small businesses such as laundromats, pizza shops, restaurants, cleaners etc. The designs should all be simple, more conservative in nature, using the colors and font of the logo. Again, think real estate Brokerage as a business context
Contact Information for Business Card
Name: Glen R. Harlow. Title: Small Business Advisor. Email: g.harlow@bayfieldcapitalworks.example. Mobile: (555) 274-3918. Office: (555) 806-2147. www.bayfieldcapitalworks.example

```html
<!DOCTYPE html>
<html lang="en">
<head>
<meta charset="utf-8">
<title>Bayfield Capital Works – Business Card</title>
<link rel="stylesheet" href="https://fonts.googleapis.com/css2?family=Roboto+Condensed:wght@400;700&display=swap">
<style>
  :root {
    --page-bg: #2b2e33;
    --card-dark: #1e1e1f;
    --card-blue: #173764;
    --brand-blue: #2a56a6;
    --brand-blue-deep: #2a3fb0;
    --brand-green: #7dc242;
    --text-light: #f2f2f2;
    --divider: #bfbfbf;
  }
  * { box-sizing: border-box; margin: 0; padding: 0; }
  html, body {
    width: 1200px; height: 780px; overflow: hidden;
    background: var(--page-bg);
  }
  .canvas {
    position: relative; width: 1200px; height: 780px;
    display: flex; align-items: center; justify-content: center; gap: 40px;
  }
  .card {
    position: relative; width: 540px; height: 309px;
    border-radius: 3px; overflow: hidden;
  }
  .card--front { background: var(--card-dark); }
  .card--back { background: var(--card-blue); }

  .brand {
    position: absolute; display: flex; align-items: center; justify-content: center; gap: 9px;
  }
  .brand__mark { width: 14px; height: 14px; flex: none; }
  .brand__name {
    font-family: "Roboto Condensed", sans-serif; font-weight: 700;
    font-size: 22px; white-space: nowrap;
  }

  .card--front .brand { top: 68px; left: 150px; width: 360px; }
  .card--front .brand__mark { background: var(--brand-green); }
  .card--front .brand__name { color: var(--brand-blue); }

  .card--back .brand { top: 136px; left: 0; width: 540px; }
  .card--back .brand__mark { background: var(--brand-blue-deep); width: 18px; height: 18px; }
  .card--back .brand__name { color: var(--brand-blue-deep); font-size: 28px; }

  .person { position: absolute; left: 42px; top: 150px; }
  .person__name {
    font-family: "Roboto Condensed", sans-serif; font-weight: 700;
    font-size: 30px; color: var(--brand-green);
  }
  .person__title {
    font-family: "Roboto Condensed", sans-serif; font-weight: 400;
    font-size: 14px; color: var(--text-light); margin-top: 2px;
  }
  .divider { position: absolute; left: 232px; top: 146px; }

  .contact-list {
    position: absolute; left: 286px; top: 160px; list-style: none;
    font-family: "Roboto Condensed", sans-serif; font-size: 13.5px;
    color: var(--text-light);
  }
  .contact-list li { display: flex; align-items: center; gap: 9px; height: 21px; white-space: nowrap; }
  .contact-list svg { width: 13px; height: 13px; flex: none; }
</style>
</head>
<body>
<main class="canvas">
  <section class="card card--front">
    <div class="brand">
      <span class="brand__mark"></span>
      <span class="brand__name">Bayfield Capital Works, Inc</span>
    </div>

    <div class="person">
      <p class="person__name">Glen R. Harlow</p>
      <p class="person__title">Small Business Advisor</p>
    </div>

    <svg class="divider" width="40" height="110" viewBox="0 0 40 110">
      <line x1="38" y1="2" x2="2" y2="108" stroke="var(--divider)" stroke-width="1"/>
    </svg>

    <ul class="contact-list">
      <li>
        <svg viewBox="0 0 14 14"><rect x="3.5" y="1" width="7" height="12" rx="1.2" fill="none" stroke="var(--brand-blue)" stroke-width="1.4"/></svg>
        (555) 274-3918
      </li>
      <li>
        <svg viewBox="0 0 14 14"><path d="M3 1.5l2.2 2.8-1.2 1.5c.8 1.8 2.3 3.3 4.1 4.1l1.5-1.2 2.8 2.2-1.4 1.6C6.3 12.5 1.6 7.8 1.5 2.9z" fill="var(--brand-green)"/></svg>
        (555) 806-2147
      </li>
      <li>
        <svg viewBox="0 0 14 14"><circle cx="7" cy="7" r="5.6" fill="none" stroke="var(--brand-blue)" stroke-width="1.3"/><ellipse cx="7" cy="7" rx="2.4" ry="5.6" fill="none" stroke="var(--brand-blue)" stroke-width="1"/><line x1="1.4" y1="7" x2="12.6" y2="7" stroke="var(--brand-blue)" stroke-width="1"/></svg>
        www.bayfieldcapitalworks.example
      </li>
      <li>
        <svg viewBox="0 0 14 14"><rect x="1" y="3" width="12" height="8.5" rx="1" fill="var(--brand-green)"/><path d="M1.5 3.6L7 8l5.5-4.4" fill="none" stroke="var(--card-dark)" stroke-width="1.1"/></svg>
        g.harlow@bayfieldcapitalworks.example
      </li>
    </ul>
  </section>

  <section class="card card--back">
    <div class="brand">
      <span class="brand__mark"></span>
      <span class="brand__name">Bayfield Capital Works, Inc</span>
    </div>
  </section>
</main>
</body>
</html>
```